The design should look similar to the uploaded example to accommodate the information needed for a business card template. I would like to see the colors orange and charcoal grey incorporated along with the logo.The following should be on the back of the card SPECIALIZING IN NEW AND USED TIRES & WHEELS FOR:- Loaders- Skid Steers- Telehandlers- Boom Lifts- Forklifs and moreELIMINATING DOWNTIMEWheel Exchange Program for New & Used Foam Filled and Solid Rubber TiresSPECIALTY SERVICES- Foam Filling Tires- Largest Tire Press in SE- ONSITE Forklift Tire Press- Boom Truck Services - Rubber Tracks

Target Market(s)

New and Existing Customers

Industry/Entity Type

Business

Contact Information for Business Card

NAMEHEAVY DUTY TIRE, LLC8470 Belvedere RoadWest Palm Beach, FL 33411P: 844-HD-TIRESF: 561-431-6469C:E: W: WWW.GRANITERIMSUPPLY-EXAMPLE.COM

Font styles to use
Sans Serif

Colors
f37122
333333

Requirements
Must have
• The logo and the information indicated for the backside of the card
Nice to have
• Keep the orange and charcoal grey colors

```html
<!DOCTYPE html>
<html lang="en">
<head>
<meta charset="utf-8">
<title>Granite Rim Supply – Business Card</title>
<link rel="stylesheet" href="https://fonts.googleapis.com/css2?family=Open+Sans:wght@400;600;700&display=swap">
<style>
  :root{
    --orange:#f37122;
    --charcoal:#333333;
    --card:#161616;
    --card-panel:#1d1d1d;
    --ink:#f2f2f2;
    --stage:#3b3b3b;
  }
  *{box-sizing:border-box;margin:0;padding:0}
  html,body{width:1200px;height:900px;overflow:hidden}
  body{background:var(--stage);font-family:"Open Sans",Arial,sans-serif;color:var(--ink);position:relative}
  .card{position:absolute;top:290px;width:530px;height:320px;border-radius:20px;background:var(--card);overflow:hidden}
  .card--front{left:50px}
  .card--back{left:620px;padding:34px 36px}

  .front__brand{position:absolute;left:0;top:0;width:210px;height:100%;display:flex;flex-direction:column;align-items:center;justify-content:center;gap:14px}
  .brand__dot{width:84px;height:84px;border-radius:50%;background:var(--orange)}
  .brand__name{font-weight:700;font-size:20px;color:var(--orange);letter-spacing:.5px;text-align:center;line-height:1.2}
  .front__info{position:absolute;left:210px;top:0;right:0;height:100%;background:var(--card-panel);padding:40px 18px 0 26px;border-left:1px solid #262626}
  .info__name{color:var(--orange);font-weight:700;font-size:18px}
  .info__company{color:var(--orange);font-weight:600;font-size:14.5px;margin-top:10px}
  .info__address{font-size:13.5px;line-height:1.4;margin-top:4px}
  .contact{list-style:none;margin-top:20px}
  .contact li{display:flex;align-items:center;gap:12px;font-size:13px;line-height:22px;white-space:nowrap}
  .contact svg{width:12px;height:12px;fill:var(--orange);flex:none}

  .back__heading{color:var(--orange);font-weight:700;text-transform:uppercase;font-size:15px;letter-spacing:.2px}
  .back__heading--large{font-size:18px}
  .back__heading--small{font-size:13px}
  .back__section{margin-bottom:18px}
  .back__text{font-size:13px;line-height:1.4;margin-top:6px;font-weight:600}
  .bullets{list-style:none;display:flex;flex-wrap:wrap;margin-top:6px;font-size:13px;font-weight:600;line-height:1.5}
  .bullets li{margin-right:12px}
  .bullets li+li::before{content:"";display:inline-block;width:7px;height:7px;border-radius:50%;background:var(--orange);margin-right:10px;vertical-align:1px}
  .bullets li.bullets__plain::before{display:none}
</style>
</head>
<body>

<section class="card card--front">
  <div class="front__brand">
    <div class="brand__dot"></div>
    <div class="brand__name">GRANITE RIM</div>
  </div>
  <div class="front__info">
    <p class="info__name">Marcus Delaney</p>
    <p class="info__company">GRANITE RIM SUPPLY, LLC</p>
    <p class="info__address">5126 Marston Lane<br>Lake Corrin, FL 33958</p>
    <ul class="contact">
      <li><svg viewBox="0 0 12 12"><path d="M2.5 0.5l2 2-1 1.5c.8 1.6 2 2.8 3.5 3.5l1.5-1 2 2-1.5 2C4.5 12 0 7.5.5 2z"/></svg>844-GR-WHEEL</li>
      <li><svg viewBox="0 0 12 12"><path d="M3 0h5v3H3zM1 4h10v6H1zM3 8h6v4H3z"/></svg>561-278-9053</li>
      <li><svg viewBox="0 0 12 12"><path d="M3 0h6a1 1 0 011 1v10a1 1 0 01-1 1H3a1 1 0 01-1-1V1a1 1 0 011-1zm0 2v7h6V2z"/></svg>123-456-7890</li>
      <li><svg viewBox="0 0 12 12"><path d="M0 2h12v8H0zM1 3l5 4 5-4v-.2H1z"/></svg>info@graniterimsupply-example.com</li>
      <li><svg viewBox="0 0 12 12"><circle cx="6" cy="6" r="5.5"/></svg>www.graniterimsupply-example.com</li>
    </ul>
  </div>
</section>

<section class="card card--back">
  <div class="back__section">
    <h2 class="back__heading">Specializing in new and used tires &amp; wheels for:</h2>
    <ul class="bullets">
      <li>Loaders</li><li>Skid Steers</li><li>Telehandlers</li><li>Boom Lifts</li>
      <li class="bullets__plain">Forklifs and more</li>
    </ul>
  </div>
  <div class="back__section">
    <h2 class="back__heading back__heading--small">Eliminating Downtime</h2>
    <p class="back__text">Wheel Exchange Program for New &amp; Used Foam<br>Filled and Solid Rubber Tires</p>
  </div>
  <div class="back__section">
    <h2 class="back__heading back__heading--large">Specialty Services</h2>
    <ul class="bullets">
      <li>Foam Filling Tires</li><li>Largest Tire Press in SE</li>
      <li class="bullets__plain">ONSITE Forklift Tire Press</li><li>Boom Truck Services</li><li>Rubber Tracks</li>
    </ul>
  </div>
</section>

</body>
</html>
```